Belmont Ridge Business Card Design Project

We have recently rebranded and would like to design new business cards that incorporate the corporate logo - double sided cards with corporate logo on one side and contact details on the other

Target Market(s)

Sophisticated and high net worth investors and finance industry professionals

Industry/Entity Type

Funds Management

Contact Information for Business Card

The card should prominently feature the company name and logo. Other details will be standard contact details for each staff member - name, address, phone, email, website

Colors
0054AA
0677BA
7BADD7
CADEEF
E8F1F8

Requirements
Must have
• Double-sided design with one side prominently featuring the corporate logo and the other side with all standard contact details

```html
<!DOCTYPE html>
<html lang="en">
<head>
<meta charset="utf-8">
<title>Belmont Ridge – Business Card</title>
<link href="https://fonts.googleapis.com/css2?family=Cinzel:wght@500&family=Arimo:wght@400&display=swap" rel="stylesheet">
<style>
  :root {
    --navy: #1f4573;
    --navy-deep: #1a3b63;
    --accent: #0054aa;
    --ink: #1c1c1c;
    --paper: #ffffff;
    --rule: #c9ccd1;
    --backdrop: #c4c4c4;
  }
  * { box-sizing: border-box; margin: 0; padding: 0; }
  html, body { width: 1200px; height: 800px; overflow: hidden; }
  body {
    background: var(--backdrop);
    display: flex;
    align-items: center;
    justify-content: center;
    gap: 40px;
  }
  .card {
    width: 540px;
    height: 309px;
    position: relative;
    overflow: hidden;
    box-shadow: 0 10px 24px rgba(0,0,0,0.25);
  }

  /* Contact side */
  .card--front { background: var(--paper); }
  .brand-band {
    position: absolute;
    left: 0; right: 0;
    top: 22px;
    height: 138px;
    background: var(--navy);
    display: flex;
    align-items: center;
    justify-content: center;
    gap: 16px;
  }
  .brand-mark {
    width: 22px; height: 22px;
    background: var(--paper);
  }
  .brand-name {
    font-family: "Cinzel", serif;
    font-weight: 500;
    font-size: 36px;
    letter-spacing: 1px;
    color: var(--paper);
  }
  .details {
    position: absolute;
    left: 0; right: 0;
    top: 180px;
    display: flex;
    justify-content: center;
    align-items: flex-start;
  }
  .person { text-align: right; padding-right: 14px; }
  .person__name {
    font-family: "Cinzel", serif;
    font-weight: 500;
    font-size: 19px;
    color: var(--navy);
    line-height: 1.1;
  }
  .person__title,
  .contact,
  .address {
    font-family: "Arimo", sans-serif;
    font-size: 13px;
    color: var(--ink);
    line-height: 1.3;
  }
  .divider {
    width: 1px;
    height: 58px;
    background: var(--rule);
  }
  .contact { padding-left: 14px; }
  .contact .domain { color: var(--accent); }
  .address {
    position: absolute;
    left: 0; right: 0;
    top: 252px;
    text-align: center;
    font-size: 14px;
  }

  /* Brand side */
  .card--back {
    background: var(--navy);
    display: flex;
    align-items: center;
    justify-content: center;
    gap: 18px;
  }
  .card--back .brand-mark {
    width: 30px; height: 30px;
    background: #2f63a3;
  }
  .card--back .brand-name {
    font-size: 40px;
    color: #2f63a3;
  }
</style>
</head>
<body>
  <section class="card card--front" aria-label="Business card, contact side">
    <div class="brand-band">
      <span class="brand-mark"></span>
      <span class="brand-name">Belmont Ridge</span>
    </div>
    <div class="details">
      <div class="person">
        <p class="person__name">Daniel Harper</p>
        <p class="person__title">Managing Director</p>
      </div>
      <div class="divider"></div>
      <div class="contact">
        <p>041-987 654 321</p>
        <p>info@belmontridge.com</p>
        <p>www.<span class="domain">belmontridge</span>.com</p>
      </div>
    </div>
    <div class="address">
      <p>Level 14, Harbour Tower, 42 Kent Lane,</p>
      <p>Sydney New South Wales 2000, Australia</p>
    </div>
  </section>

  <section class="card card--back" aria-label="Business card, brand side">
    <span class="brand-mark"></span>
    <span class="brand-name">Belmont Ridge</span>
  </section>
</body>
</html>
```